Velmo Swinger site - new website, blogsite and merchandise point, connection to tradeva

We are a well established Swingers Club in the North east of UK and already have an existing site. www.velmo-example.co.uk, BUT we have changed our logo and our information on the site needs to be updated.

We are changing our hosting site to Nimbrashost.example ,also wanting to start a blog which is linked to the club, plus we wish to sell a small exclusive range of Velmo linked merchandise which will also be available on Tradeva.

I have attached a pdf of the majority of the content. additionally we will provide pictures and a videoclip which should be able to be viewed by pc's, lap tops and mobile phones (the whole website must be fully accessible via phone).

The new site must be able to be updated by someone with medium computer knowledge (usually me), by no means expert. Updates will generally be new pictures and written information. The site must be able to be transferred to NimbrasHost.

Velmo is one of the countries leading clubs and emphasises friendliness, fun & safety for its members, we look after you to ensure your experience is the best we can offer. We are very proud of our reputation, built up over more than 10 years.

Target Market(s)

Swingers, dreamers & fantasists, alternative lifestyle people

Coding

Coded - Design and coding required

Number of Pages Required

5+ page

Font styles to use
Sans Serif

Colors
000000
ec1f27
fbfbfb
eeeeee
eaeaea

Requirements
Must have
• website with blog attached, link to tradeva & quidlo, ability to run videoclip and picture album and must be compatable to transfer easily to Nimbrashost and be updated by non-professional (who can learn)
• Straightforward & easy to navigate
• over 18 content page with enter button
Nice to have
• sexy site
• link to chirpster maybe
• black site would be nice with red or white writing
Should not have
• children and animals in anyway shape or form

```html
<!DOCTYPE html>
<html lang="en">
<head>
<meta charset="utf-8">
<title>Velmo — Swingers Club North East</title>
<link rel="stylesheet" href="https://fonts.googleapis.com/css2?family=Cinzel:wght@400;700&family=Open+Sans:wght@400;600;700&display=swap">
<style>
:root{
  --black:#000000;
  --red:#ec1f27;
  --red-deep:#c8161d;
  --white:#fbfbfb;
  --light:#eeeeee;
  --light-2:#eaeaea;
  --grey:#9a9a9a;
  --dark:#1b1b1b;
  --dark-2:#262626;
  --serif:'Cinzel', Georgia, serif;
  --sans:'Open Sans', Arial, sans-serif;
}
*{box-sizing:border-box;margin:0;padding:0}
html,body{width:1200px;height:4100px;overflow:hidden}
body{position:relative;background:var(--black);color:var(--white);font-family:var(--sans)}
.abs{position:absolute}
section,header,footer{position:absolute;left:0;width:1200px;overflow:hidden}
.bg{position:absolute;inset:0}

/* header + hero */
.hero{top:0;height:533px}
.hero .bg{background:linear-gradient(180deg,#0d1424 0%,#1e2a40 40%,#3a3024 75%,#17130f 100%)}
.hero .shade{position:absolute;inset:0;background:rgba(0,0,0,.25)}
.logo{left:96px;top:30px;font-family:var(--serif);font-size:40px;letter-spacing:2px;color:var(--white)}
.topbar{right:100px;top:12px;font-size:14px;display:flex;gap:14px;align-items:center;color:var(--white)}
.topbar svg{vertical-align:-2px;margin-right:6px}
.topbar .sep{opacity:.6}
.mainnav{right:100px;top:56px;display:flex;gap:16px;font-size:15px;align-items:center}
.mainnav a{color:var(--white);text-decoration:none}
.mainnav a.active{color:var(--red)}
.hero-title{left:0;width:1200px;top:160px;text-align:center;font-family:var(--serif);font-size:78px;letter-spacing:18px;color:var(--white)}
.hero-tag{left:0;width:1200px;top:258px;text-align:center;font-size:23px;font-weight:700;line-height:36px}
.btn-outline{left:514px;top:350px;width:172px;height:46px;border:2px solid var(--white);border-radius:3px;font-size:14px;font-weight:600;display:flex;align-items:center;justify-content:center;letter-spacing:.5px}
.dots{left:563px;top:470px;display:flex;gap:9px}
.dots span{width:11px;height:11px;border-radius:50%;border:2px solid var(--white)}
.dots span.on{background:var(--white)}

/* welcome */
.welcome{top:533px;height:711px;background:var(--red)}
.welcome .bg{background:linear-gradient(180deg,rgba(236,31,39,.9),rgba(200,22,29,.92)),linear-gradient(90deg,#7a0d12,#b4161c 50%,#6a0b10)}
h2.section-title{position:absolute;left:0;width:1200px;text-align:center;font-family:var(--serif);font-weight:400;font-size:40px;color:var(--white)}
.welcome h2{top:58px}
.welcome .intro{left:210px;width:780px;top:150px;text-align:center;font-size:14px;line-height:28px}
.feature{width:240px;text-align:center}
.feature svg{display:block;margin:0 auto 18px}
.feature h3{font-family:var(--sans);font-weight:400;font-size:17px;letter-spacing:.5px;text-transform:uppercase;margin-bottom:8px}
.feature p{font-size:12.5px;line-height:20px}

/* about */
.about{top:1244px;height:506px}
.about .bg{background:linear-gradient(90deg,#1a0807,#3a100c 40%,#230a08)}
.about-photo{left:100px;top:66px;width:406px;height:380px;border:2px solid var(--light-2);background:linear-gradient(135deg,#5a0e10,#b2232a 50%,#2a0808)}
.about h2{position:absolute;left:558px;top:62px;font-family:var(--serif);font-weight:400;font-size:36px;line-height:46px}
.about .copy{left:558px;top:172px;width:540px;font-size:13px;line-height:24px}
.about .copy p{margin-bottom:18px}
.btn-ghost-red{left:558px;top:400px;width:128px;height:40px;border:2px solid var(--red);color:var(--white);font-size:12px;font-weight:600;display:flex;align-items:center;justify-content:center;border-radius:2px}

/* membership */
.membership{top:1750px;height:382px}
.membership .bg{background:linear-gradient(180deg,#141414,#2b2b2b 50%,#161616)}
.card{top:95px;width:480px;height:215px;border:2px solid var(--light-2);background:rgba(0,0,0,.85);display:flex}
.card .pic{width:200px;height:100%}
.card .body{padding:18px 16px 0 18px;flex:1}
.card h4{font-family:var(--serif);font-weight:400;color:var(--red);font-size:19px;margin-bottom:10px}
.card p{font-size:12.5px;line-height:20px;margin-bottom:16px}
.btn-red{display:inline-block;background:var(--red);color:var(--white);font-size:12px;font-weight:700;padding:11px 26px;border-radius:2px}

/* blog */
.blog{top:2132px;height:410px}
.blog .bg{background:linear-gradient(90deg,#1d0807,#3a0c0a 50%,#1a0706)}
.blog h2{top:60px}
.post{top:162px;width:500px;display:flex;gap:20px}
.post .pic{width:200px;height:175px;flex:none}
.post h5{font-family:var(--sans);font-weight:400;font-size:15px;line-height:22px;text-transform:uppercase;margin-bottom:12px}
.post .meta{font-size:12px;color:var(--light);margin-bottom:12px;display:flex;gap:12px;align-items:center}
.post .meta svg{margin-right:4px;vertical-align:-1px}
.post p{font-size:12.5px;line-height:19px;margin-bottom:12px}
.post .more{font-size:12px;color:var(--red);font-weight:700}

/* products */
.products{top:2542px;height:1285px}
.products .bg{background:linear-gradient(180deg,#242424,#151515 40%,#202020)}
.products h2{top:58px}
.product{width:235px}
.product .thumb{height:216px;background:var(--white);display:flex;align-items:center;justify-content:center}
.product .thumb.soon span{font-size:21px;font-weight:700;color:#b8b8b8;letter-spacing:.5px}
.product .thumb .art{width:150px;height:180px;border-radius:6px}
.product p{font-size:13.5px;line-height:22px;margin:22px 0 10px;color:var(--white)}
.product .row{display:flex;justify-content:space-between;align-items:center}
.product .price{color:var(--red);font-weight:700;font-size:14px}
.product .store{font-weight:700;font-size:15px;color:var(--white)}

/* footer */
.site-footer{top:3827px;height:273px;background:#0a0a0a;border-top:3px solid var(--red)}
.contact-row{left:0;width:1200px;top:60px;display:flex;justify-content:center;gap:60px;font-size:14px;align-items:center}
.contact-row .item{display:flex;align-items:center;gap:14px;line-height:20px}
.icon-ring{width:44px;height:44px;border-radius:50%;border:2px solid var(--light);display:flex;align-items:center;justify-content:center;flex:none}
.footnav{left:0;width:1200px;top:160px;display:flex;justify-content:center;gap:24px;font-size:14px;font-weight:600}
.rule{left:100px;width:1000px;top:205px;height:1px;background:#333}
.copyright{left:100px;top:232px;font-size:12.5px;color:var(--light)}
.social{right:100px;top:222px;display:flex;gap:8px}
.social span{width:32px;height:32px;border-radius:50%;border:2px solid var(--light)}
</style>
</head>
<body>

<header class="hero">
  <div class="bg" role="img" aria-label="Night view of a city skyline with a lit cathedral on the hill"></div>
  <div class="shade"></div>
  <div class="abs logo">VELMO</div>
  <div class="abs topbar">
    <span><svg width="13" height="13" viewBox="0 0 24 24"><path fill="#ec1f27" d="M6.6 10.8a15 15 0 0 0 6.6 6.6l2.2-2.2c.3-.3.7-.4 1-.2 1.1.4 2.3.6 3.6.6.6 0 1 .4 1 1V20c0 .6-.4 1-1 1A17 17 0 0 1 3 4c0-.6.4-1 1-1h3.5c.6 0 1 .4 1 1 0 1.3.2 2.5.6 3.6.1.3 0 .7-.2 1z"/></svg>0700 555 0192</span>
    <span class="sep">|</span>
    <span><svg width="14" height="11" viewBox="0 0 24 18"><rect width="24" height="18" rx="2" fill="#ec1f27"/><path d="M1 2l11 8 11-8" stroke="#fff" stroke-width="2" fill="none"/></svg>velmoswingers@mail.example</span>
  </div>
  <nav class="abs mainnav">
    <a class="active">Home</a><a>Diary</a><a>Theme Parties</a><a>TV/TG and Admirers</a><a>Membership</a><a>FAQs</a><a>Rooms</a><a>Contact Us</a><a>Links</a>
    <svg width="15" height="15" viewBox="0 0 24 24"><circle cx="10" cy="10" r="7" stroke="#fbfbfb" stroke-width="3" fill="none"/><path d="M15 15l7 7" stroke="#fbfbfb" stroke-width="3"/></svg>
  </nav>
  <div class="abs hero-title">VELMO</div>
  <div class="abs hero-tag">We are a Swingers Club in the UK Velmo is one of the countries leading clubs<br>and emphasises friendliness, fun &amp; safety for its members.</div>
  <div class="abs btn-outline">GET MORE INFO</div>
  <div class="abs dots"><span class="on"></span><span></span><span></span><span></span></div>
</header>

<section class="welcome">
  <div class="bg" role="img" aria-label="Club room interior tinted in red"></div>
  <h2 class="section-title">Welcome to Velmo</h2>
  <p class="abs intro">We are the best in the North East, and have recently been voted No 2 club in the UK. We have retained the coveted title of No 1 friendliest club in the UK (in joint 1st place with our great friends "The Open Door", London).</p>

  <div class="abs feature" style="left:80px;top:235px">
    <svg width="50" height="50" viewBox="0 0 24 24"><circle cx="18" cy="5" r="3" fill="#fff"/><circle cx="6" cy="12" r="3" fill="#fff"/><circle cx="18" cy="19" r="3" fill="#fff"/><path d="M6 12L18 5M6 12l12 7" stroke="#fff" stroke-width="2"/></svg>
    <h3>Social Area</h3><p>Nam libero tempore cum solutax<br>nobis est eligendi sert optio</p>
  </div>
  <div class="abs feature" style="left:345px;top:235px">
    <svg width="58" height="50" viewBox="0 0 28 24"><path d="M7 6h14a6 6 0 0 1 6 6v3a4 4 0 0 1-7 2l-2-2h-8l-2 2a4 4 0 0 1-7-2v-3a6 6 0 0 1 6-6z" fill="#fff"/><path d="M8 10v5M5.5 12.5h5" stroke="#ec1f27" stroke-width="1.6"/><circle cx="19" cy="11" r="1.2" fill="#ec1f27"/><circle cx="22" cy="14" r="1.2" fill="#ec1f27"/></svg>
    <h3>Play Rooms</h3><p>Nam libero tempore cum solutax<br>nobis est eligendi sert optio</p>
  </div>
  <div class="abs feature" style="left:610px;top:235px">
    <svg width="50" height="50" viewBox="0 0 24 24"><path d="M3 22V11a9 9 0 0 1 18 0v11h-5V12a4 4 0 0 0-8 0v10z" fill="#fff"/></svg>
    <h3>Tams Dungeon</h3><p>Nam libero tempore cum solutax<br>nobis est eligendi sert optio</p>
  </div>
  <div class="abs feature" style="left:878px;top:235px">
    <svg width="50" height="50" viewBox="0 0 24 24"><path d="M2 3h20l-2 6H4z" fill="#fff"/><rect x="4" y="10" width="16" height="12" fill="#fff"/><rect x="8" y="14" width="8" height="8" fill="#ec1f27"/></svg>
    <h3>Exhibition Area</h3><p>Nam libero tempore cum solutax<br>nobis est eligendi sert optio</p>
  </div>

  <div class="abs feature" style="left:80px;top:448px">
    <svg width="50" height="50" viewBox="0 0 24 24"><path d="M6 23V6l6-5 6 5v17z" fill="#fff"/><g fill="#ec1f27"><rect x="9" y="8" width="2" height="3"/><rect x="13" y="8" width="2" height="3"/><rect x="9" y="13" width="2" height="3"/><rect x="13" y="13" width="2" height="3"/><rect x="10.5" y="18" width="3" height="5"/></g></svg>
    <h3>Amsterdam Room</h3><p>Nam libero tempore cum solutax<br>nobis est eligendi sert optio</p>
  </div>
  <div class="abs feature" style="left:345px;top:448px">
    <svg width="50" height="50" viewBox="0 0 24 24"><path d="M12 1C8 8 5 12 5 16a7 7 0 0 0 14 0c0-4-3-8-7-15z" fill="#fff"/></svg>
    <h3>Wet Areas</h3><p>Nam libero tempore cum solutax<br>nobis est eligendi sert optio</p>
  </div>
  <div class="abs feature" style="left:610px;top:448px">
    <svg width="50" height="50" viewBox="0 0 24 24"><rect x="5" y="2" width="14" height="21" fill="#fff"/><g fill="#ec1f27"><rect x="8" y="5" width="3" height="3"/><rect x="13" y="5" width="3" height="3"/><rect x="8" y="10" width="3" height="3"/><rect x="13" y="10" width="3" height="3"/><rect x="10" y="17" width="4" height="6"/></g></svg>
    <h3>Hotel Rooms</h3><p>Nam libero tempore cum solutax<br>nobis est eligendi sert optio</p>
  </div>
  <div class="abs feature" style="left:878px;top:448px">
    <svg width="50" height="50" viewBox="0 0 24 24"><circle cx="13" cy="13" r="8" fill="#fff"/><path d="M1 5l7 4M4 2l5 6M7 1l3 6" stroke="#fff" stroke-width="1.6"/><circle cx="15" cy="12" r="2" fill="#ec1f27"/></svg>
    <h3>Crash Space</h3><p>Nam libero tempore cum solutax<br>nobis est eligendi sert optio</p>
  </div>
</section>

<section class="about">
  <div class="bg" role="img" aria-label="Dim club interior with warm red lighting"></div>
  <div class="abs about-photo" role="img" aria-label="Red-lit dungeon room with a cross frame and a platform"></div>
  <h2>Velmo :: A Great<br>Place To Meet And Play!</h2>
  <div class="abs copy">
    <p>We are the best Swingers Club in the North East, and also voted No 2 club in the UK.</p>
    <p>We have retained the coveted title of No 1 friendliest club in the UK (in joint 1st place with our great friends "The Open Door", London). This prestigious award has been given to us by a panel of &amp;quot;mystery sisters&amp;quot; (swingers, singles &amp; couples) working with the publication called "Nights Out North" a copy of whichis available in reception. Please see our Frequently Asked Questions and Membership pages for more information about the club and its facilities. Velmo was established in Sunderland in 2004 by Alex.</p>
  </div>
  <div class="abs btn-ghost-red">READ MORE</div>
</section>

<section class="membership">
  <div class="bg" role="img" aria-label="Monochrome club lounge interior"></div>
  <div class="abs card" style="left:100px">
    <div class="pic" role="img" aria-label="Boudoir room with a patterned bed and lamps" style="background:linear-gradient(135deg,#6b1f14,#c0532b 45%,#3a1510)"></div>
    <div class="body"><h4>Membership Fees</h4><p>New members (Couples and Single guys) - (annual) £30, this now includes the next 2 visits half price.</p><span class="btn-red">READ MORE</span></div>
  </div>
  <div class="abs card" style="left:620px">
    <div class="pic" role="img" aria-label="Hotel room with a bed and framed art" style="background:linear-gradient(135deg,#3a1b14,#a2402c 50%,#2a1410)"></div>
    <div class="body"><h4>Membership Discounts</h4><p>We discount every and membership to support Her Majesty's Forces (serving and retired)..</p><span class="btn-red">READ MORE</span></div>
  </div>
</section>

<section class="blog">
  <div class="bg" role="img" aria-label="Dark red club interior"></div>
  <h2 class="section-title">Our Blog</h2>
  <article class="abs post" style="left:100px">
    <div class="pic" role="img" aria-label="Bar area with warm lights" style="background:linear-gradient(135deg,#2a1608,#8a5a22 50%,#1a0e06)"></div>
    <div>
      <h5>At vero eos et accusamus et iusto odio dignipra</h5>
      <div class="meta"><span><svg width="11" height="11" viewBox="0 0 12 12"><rect x="1" y="2" width="10" height="9" fill="none" stroke="#eee"/><path d="M1 5h10" stroke="#eee"/></svg>17/06/2017</span><span>|</span><span><svg width="11" height="11" viewBox="0 0 12 12"><circle cx="6" cy="4" r="2.5" fill="#eee"/><path d="M1 12a5 5 0 0 1 10 0z" fill="#eee"/></svg>Alex</span></div>
      <p>Nam libero tempore, cum soluta nobis eleidi optio cumque nihil impedo</p>
      <span class="more">READ MORE &gt;&gt;</span>
    </div>
  </article>
  <article class="abs post" style="left:630px">
    <div class="pic" role="img" aria-label="Wine cellar with bottle racks" style="background:linear-gradient(135deg,#1a120c,#6a4a30 50%,#140c08)"></div>
    <div>
      <h5>At vero eos et accusamus et iusto odio dignipra</h5>
      <div class="meta"><span><svg width="11" height="11" viewBox="0 0 12 12"><rect x="1" y="2" width="10" height="9" fill="none" stroke="#eee"/><path d="M1 5h10" stroke="#eee"/></svg>17/06/2017</span><span>|</span><span><svg width="11" height="11" viewBox="0 0 12 12"><circle cx="6" cy="4" r="2.5" fill="#eee"/><path d="M1 12a5 5 0 0 1 10 0z" fill="#eee"/></svg>Alex</span></div>
      <p>Nam libero tempore, cum soluta nobis eleidi optio cumque nihil impedo</p>
      <span class="more">READ MORE &gt;&gt;</span>
    </div>
  </article>
</section>

<section class="products">
  <div class="bg" role="img" aria-label="Monochrome club room backdrop"></div>
  <h2 class="section-title">Velmo Products</h2>

  <div class="abs product" style="left:100px;top:145px"><div class="thumb"><div class="art" role="img" aria-label="Black t-shirt with Velmo print" style="background:#111"></div></div><p>At vero eos et accusamus euto<br>odio dignissimos duc.</p><div class="row"><span class="price">$20.00</span><span class="store">tradeva</span></div></div>
  <div class="abs product" style="left:355px;top:145px"><div class="thumb"><div class="art" role="img" aria-label="Red mug with Velmo print" style="background:linear-gradient(135deg,#ec1f27,#a9141a)"></div></div><p>At vero eos et accusamus euto<br>odio dignissimos duc.</p><div class="row"><span class="price">$20.00</span><span class="store">tradeva</span></div></div>
  <div class="abs product" style="left:610px;top:145px"><div class="thumb"><div class="art" role="img" aria-label="Dark wine bottle with Velmo label" style="width:60px;background:linear-gradient(180deg,#2a2a2a,#0a0a0a)"></div></div><p>At vero eos et accusamus euto<br>odio dignissimos duc.</p><div class="row"><span class="price">$20.00</span><span class="store">tradeva</span></div></div>
  <div class="abs product" style="left:865px;top:145px"><div class="thumb"><div class="art" role="img" aria-label="Red cap with Velmo print" style="height:120px;background:linear-gradient(135deg,#ec1f27,#b3151c)"></div></div><p>At vero eos et accusamus euto<br>odio dignissimos duc.</p><div class="row"><span class="price">$20.00</span><span class="store">tradeva</span></div></div>

  <div class="abs product" style="left:100px;top:514px"><div class="thumb soon"><span>COMING SOON</span></div><p>At vero eos et accusamus euto<br>odio dignissimos duc.</p><div class="row"><span class="price">$20.00</span><span class="store">tradeva</span></div></div>
  <div class="abs product" style="left:355px;top:514px"><div class="thumb soon"><span>COMING SOON</span></div><p>At vero eos et accusamus euto<br>odio dignissimos duc.</p><div class="row"><span class="price">$20.00</span><span class="store">tradeva</span></div></div>
  <div class="abs product" style="left:610px;top:514px"><div class="thumb soon"><span>COMING SOON</span></div><p>At vero eos et accusamus euto<br>odio dignissimos duc.</p><div class="row"><span class="price">$20.00</span><span class="store">tradeva</span></div></div>
  <div class="abs product" style="left:865px;top:514px"><div class="thumb soon"><span>COMING SOON</span></div><p>At vero eos et accusamus euto<br>odio dignissimos duc.</p><div class="row"><span class="price">$20.00</span><span class="store">tradeva</span></div></div>

  <div class="abs product" style="left:100px;top:891px"><div class="thumb soon"><span>COMING SOON</span></div><p>At vero eos et accusamus euto<br>odio dignissimos duc.</p><div class="row"><span class="price">$20.00</span><span class="store">tradeva</span></div></div>
  <div class="abs product" style="left:355px;top:891px"><div class="thumb soon"><span>COMING SOON</span></div><p>At vero eos et accusamus euto<br>odio dignissimos duc.</p><div class="row"><span class="price">$20.00</span><span class="store">tradeva</span></div></div>
  <div class="abs product" style="left:610px;top:891px"><div class="thumb soon"><span>COMING SOON</span></div><p>At vero eos et accusamus euto<br>odio dignissimos duc.</p><div class="row"><span class="price">$20.00</span><span class="store">tradeva</span></div></div>
  <div class="abs product" style="left:865px;top:891px"><div class="thumb soon"><span>COMING SOON</span></div><p>At vero eos et accusamus euto<br>odio dignissimos duc.</p><div class="row"><span class="price">$20.00</span><span class="store">tradeva</span></div></div>
</section>

<footer class="site-footer">
  <div class="abs contact-row">
    <div class="item"><span class="icon-ring"><svg width="16" height="20" viewBox="0 0 16 22"><path d="M8 0a8 8 0 0 1 8 8c0 6-8 14-8 14S0 14 0 8a8 8 0 0 1 8-8z" fill="#eee"/><circle cx="8" cy="8" r="3" fill="#0a0a0a"/></svg></span><span>12 Harbour Row, 3rd Floor<br>London</span></div>
    <div class="item"><span class="icon-ring"><svg width="18" height="18" viewBox="0 0 24 24"><path fill="#eee" d="M6.6 10.8a15 15 0 0 0 6.6 6.6l2.2-2.2c.3-.3.7-.4 1-.2 1.1.4 2.3.6 3.6.6.6 0 1 .4 1 1V20c0 .6-.4 1-1 1A17 17 0 0 1 3 4c0-.6.4-1 1-1h3.5c.6 0 1 .4 1 1 0 1.3.2 2.5.6 3.6.1.3 0 .7-.2 1z"/></svg></span><span>0700 555 0192</span></div>
    <div class="item"><span class="icon-ring"><svg width="18" height="14" viewBox="0 0 24 18"><rect width="24" height="18" rx="2" fill="#eee"/><path d="M1 2l11 8 11-8" stroke="#0a0a0a" stroke-width="2" fill="none"/></svg></span><span>velmoswingers@mail.example</span></div>
  </div>
  <nav class="abs footnav"><span>HOME</span><span>DIARY</span><span>THEME PARTIES</span><span>TV/TG AND ADMIRERS</span><span>MEMBERSHIP</span><span>FAQS</span><span>ROOMS</span><span>CONTACT US</span><span>LINKS</span></nav>
  <div class="abs rule"></div>
  <div class="abs copyright">Copyrights © 2017, Velmo. All rights reserved.</div>
  <div class="abs social" aria-label="Social links"><span></span><span></span><span></span></div>
</footer>

</body>
</html>
```